Business card - Harbor Crest Builders

Design a business card utilizing the given logo.
colors we like: Black, greys, Teal, blues.
Tri color card, horizontal orientation likely
Logo and name likely best on top.
Info on card:

Dennis Farrow
#8 - 4815 Alder Ridge Blvd.
Surrey, B.C. V3K 2R9

778.555.0193
dennisfarrow@tellmail.ca

Slogan: "Building Dreams"

We are a construction company that specializes in new home construction on the West coast of BC Canada. Open Concepts designs of high end homes.

```html
<!DOCTYPE html>
<html lang="en">
<head>
<meta charset="utf-8">
<title>Harbor Crest Builders – Business Card</title>
<link rel="stylesheet" href="https://fonts.googleapis.com/css2?family=Andika:wght@700&family=Ubuntu:wght@500&display=swap">
<style>
  :root {
    --grey-light: #f7f8f8;
    --grey-mid: #c3c8ca;
    --grey-dark: #8e9599;
    --band-dark: #1b1d1f;
    --band-mid: #34383b;
    --blue-light: #7cc6f4;
    --blue-mid: #3a8fd6;
    --blue-deep: #1c58a0;
    --navy-edge: #0b1f3a;
    --ink: #141414;
    --slogan-light: #ffffff;
    --slogan-shade: #9aa1a6;
  }
  * { margin: 0; padding: 0; box-sizing: border-box; }
  html, body {
    width: 1200px; height: 702px; overflow: hidden;
    background: var(--grey-mid);
  }
  .card {
    position: relative;
    width: 1200px; height: 702px;
    overflow: hidden;
    background: radial-gradient(ellipse 620px 420px at 590px 330px,
      var(--grey-light) 0%, var(--grey-mid) 62%, var(--grey-dark) 100%);
    font-family: "Andika", "Trebuchet MS", sans-serif;
  }
  .base-band {
    position: absolute; left: 0; top: 0;
    width: 1200px; height: 702px;
  }
  .brand {
    position: absolute; left: 56px; top: 62px;
    display: flex; align-items: center; gap: 22px;
  }
  .brand-dot {
    width: 96px; height: 96px; border-radius: 50%;
    background: var(--ink);
  }
  .brand-name {
    font-size: 38px; font-weight: 700; color: var(--ink);
    line-height: 1;
  }
  .blue-text {
    background: linear-gradient(180deg, var(--blue-light) 0%, var(--blue-mid) 50%, var(--blue-deep) 100%);
    -webkit-background-clip: text; background-clip: text;
    color: transparent;
    filter: drop-shadow(1px 1px 0 var(--navy-edge)) drop-shadow(2px 2px 1px rgba(0,0,0,.45));
    font-weight: 700;
    white-space: nowrap;
  }
  .contact-head {
    position: absolute; left: 660px; top: 58px; width: 480px;
    text-align: center;
  }
  .person-name { font-size: 42px; letter-spacing: 4px; line-height: 1.1; }
  .phone { font-size: 42px; letter-spacing: 4px; line-height: 1.15; }
  .contact-foot {
    position: absolute; left: 0; top: 400px; width: 1200px;
    text-align: center; padding-right: 20px;
  }
  .email { font-size: 34px; letter-spacing: 2px; line-height: 1.3; margin-left: -10px; }
  .address { font-size: 42px; letter-spacing: 3px; line-height: 1.22; }
  .slogan {
    position: absolute; left: 0; top: 615px; width: 1150px;
    text-align: center;
    font-family: "Ubuntu", "Segoe UI", sans-serif;
    font-weight: 500; font-size: 54px; letter-spacing: 4px;
    background: linear-gradient(180deg, var(--slogan-light) 20%, var(--slogan-shade) 100%);
    -webkit-background-clip: text; background-clip: text;
    color: transparent;
  }
</style>
</head>
<body>
  <main class="card">
    <svg class="base-band" viewBox="0 0 1200 702" aria-hidden="true">
      <defs>
        <linearGradient id="bandFill" x1="0" y1="0" x2="0" y2="1">
          <stop offset="0" stop-color="#2a2d30"/>
          <stop offset="0.5" stop-color="#1b1d1f"/>
          <stop offset="1" stop-color="#101112"/>
        </linearGradient>
      </defs>
      <path d="M0 500 Q600 690 1200 500 L1200 702 L0 702 Z" fill="url(#bandFill)"/>
    </svg>

    <div class="brand">
      <span class="brand-dot"></span>
      <span class="brand-name">Harbor Crest Builders</span>
    </div>

    <div class="contact-head">
      <p class="person-name blue-text">DENNIS FARROW</p>
      <p class="phone blue-text">778.555.0193</p>
    </div>

    <div class="contact-foot">
      <p class="email blue-text">dennisfarrow@tellmail.ca</p>
      <p class="address blue-text">#8 - 4815 Alder Ridge Blvd.</p>
      <p class="address blue-text">Surrey, B.C. V3K 2R9</p>
    </div>

    <p class="slogan">BUILDING DREAMS</p>
  </main>
</body>
</html>
```